Professional Package for CPA Firm

We would like a stationery design for our new CPA Firm based in Atlanta, GA called 'Vale 8'. We work with investors to help grow investments, tax free. We would like the design to have a professional/minimal look with a 'wow' factor. We need 9.5″ x 4.125″, 9x12, and 10x13 mailing envelopes, business cards, and a letterhead. We have a logo that is already complete. For the letterhead, we would like to have space to put credentials at the bottom of the page

Industry/Entity Type

CPA, Accounting

```html
<!DOCTYPE html>
<html lang="en">
<head>
<meta charset="utf-8">
<title>Vale 8 — Stationery</title>
<link href="https://fonts.googleapis.com/css2?family=Montserrat:wght@400;600;800&display=swap" rel="stylesheet">
<style>
  :root {
    --brand-blue: #1f9ad6;
    --brand-blue-light: #8fd0f0;
    --ink: #1c1c1c;
    --ink-soft: #4a4a4a;
    --paper: #ffffff;
    --stage: #e9eaec;
    --stage-dark: #3a3a3c;
    --rule: #d7d9dc;
  }
  * { box-sizing: border-box; margin: 0; padding: 0; }
  html, body { width: 1200px; height: 3488px; overflow: hidden; }
  body { background: var(--stage); font-family: "Montserrat", sans-serif; color: var(--ink); position: relative; }

  .section { position: absolute; left: 0; width: 1200px; }
  .section--cards { top: 0; height: 900px; background: var(--stage-dark); }
  .section--letter { top: 900px; height: 795px; }
  .section--dl { top: 1695px; height: 785px; border-top: 1px solid var(--rule); }
  .section--large { top: 2480px; height: 1008px; border-top: 1px solid var(--rule); }

  .sheet { position: absolute; background: var(--paper); box-shadow: 0 10px 30px rgba(0,0,0,.12); }

  .wordmark { font-weight: 800; letter-spacing: 1px; color: var(--ink); display: flex; align-items: center; gap: 10px; line-height: 1; }
  .wordmark__dot { width: 18px; height: 18px; background: var(--brand-blue); border-radius: 50%; display: inline-block; }
  .tagline { font-weight: 400; color: var(--ink-soft); letter-spacing: .5px; }

  /* business card */
  .card { width: 560px; height: 320px; top: 300px; }
  .card--front { left: 50px; display: flex; align-items: center; padding: 0 40px; }
  .card--front .brand { width: 210px; }
  .card--front .wordmark { font-size: 40px; }
  .card--front .tagline { font-size: 12px; margin-top: 8px; }
  .card__divider { width: 2px; height: 170px; background: var(--ink); margin: 0 30px; }
  .card__person .name { font-weight: 800; font-size: 18px; text-transform: uppercase; }
  .card__person .role { font-weight: 600; font-size: 15px; color: var(--brand-blue); margin-bottom: 14px; }
  .card__person p { font-size: 13px; line-height: 1.55; color: var(--ink-soft); }
  .contact { display: flex; align-items: center; gap: 8px; }
  .contact svg { width: 13px; height: 13px; flex: none; }
  .card--back { left: 630px; background: var(--brand-blue); display: flex; flex-direction: column; align-items: center; justify-content: center; }
  .card--back .wordmark { font-size: 54px; color: var(--brand-blue-light); }
  .card--back .tagline { color: var(--brand-blue-light); font-size: 15px; margin-top: 10px; }

  /* letterhead */
  .letterhead { left: 90px; top: 60px; width: 520px; height: 673px; padding: 44px 46px; }
  .letterhead__head { display: flex; justify-content: space-between; align-items: flex-start; margin-bottom: 34px; }
  .letterhead .wordmark { font-size: 26px; }
  .letterhead .tagline { font-size: 8px; margin-top: 5px; }
  .letterhead__address { font-size: 8px; line-height: 1.6; color: var(--ink-soft); text-align: right; }
  .letterhead__body { font-size: 9px; line-height: 1.7; color: var(--ink-soft); }
  .letterhead__body p { margin-bottom: 12px; }
  .letterhead__credentials { position: absolute; left: 46px; right: 46px; bottom: 36px; border-top: 1px solid var(--rule); height: 40px; }

  /* envelopes */
  .envelope-back .flap { position: absolute; left: 0; right: 0; top: 0; background: var(--brand-blue); border-radius: 0 0 10px 10px; display: flex; align-items: center; justify-content: center; }
  .envelope-back .flap .wordmark { color: var(--paper); }
  .dl { width: 560px; height: 243px; }
  .dl--letter { left: 620px; top: 380px; }
  .dl .flap { height: 74px; }
  .dl .flap .wordmark { font-size: 18px; }
  .dl--back { left: 560px; top: 90px; }
  .dl--front { left: 80px; top: 360px; width: 620px; height: 270px; padding: 36px 40px; }
  .dl--front .wordmark { font-size: 28px; }
  .dl--front .tagline, .address { font-size: 10px; }
  .address { line-height: 1.5; color: var(--ink-soft); margin-top: 6px; }

  .catalog { left: 120px; top: 110px; width: 420px; height: 620px; }
  .catalog .flap { height: 84px; border-radius: 0 0 4px 4px; }
  .catalog .flap .wordmark { display: none; }
  .catalog-front { left: 560px; top: 230px; width: 440px; height: 572px; display: flex; flex-direction: column; align-items: center; padding-top: 60px; text-align: center; }
  .catalog-front .wordmark { font-size: 28px; }
  .catalog-front .tagline { font-size: 10px; margin-top: 6px; }
</style>
</head>
<body>

<section class="section section--cards">
  <article class="sheet card card--front">
    <div class="brand">
      <div class="wordmark"><span class="wordmark__dot"></span>VALE 8</div>
      <div class="tagline">CPAs and Tax Advisors</div>
    </div>
    <div class="card__divider"></div>
    <div class="card__person">
      <div class="name">Daniel Marlow</div>
      <div class="role">Managing Director</div>
      <p>14 Harbor Ridge Lane,<br>Lakeview, ON K2B 7M1</p>
      <p class="contact"><svg viewBox="0 0 16 16"><path fill="#1f9ad6" d="M3 1h3l1.5 4-2 1.2a9 9 0 0 0 4.3 4.3L11 8.5l4 1.5v3a2 2 0 0 1-2 2A12 12 0 0 1 1 3a2 2 0 0 1 2-2z"/></svg>+5550123456</p>
      <p class="contact"><svg viewBox="0 0 16 16"><rect x="1" y="3" width="14" height="10" rx="1" fill="#1f9ad6"/><path d="M1 4l7 5 7-5" stroke="#fff" fill="none"/></svg>info@valeeight.com</p>
      <p class="contact"><svg viewBox="0 0 16 16"><circle cx="8" cy="8" r="6.5" fill="none" stroke="#1f9ad6" stroke-width="1.5"/><path d="M1.5 8h13M8 1.5c-3 3.5-3 9.5 0 13M8 1.5c3 3.5 3 9.5 0 13" stroke="#1f9ad6" fill="none"/></svg>www.valeeight.com</p>
    </div>
  </article>
  <article class="sheet card card--back">
    <div class="wordmark">VALE 8</div>
    <div class="tagline">CPAs and Tax Advisors</div>
  </article>
</section>

<section class="section section--letter">
  <article class="sheet letterhead">
    <header class="letterhead__head">
      <div>
        <div class="wordmark">VALE 8</div>
        <div class="tagline">CPAs and Tax Advisors</div>
      </div>
      <div class="letterhead__address">14 Harbor Ridge Lane,<br>Lakeview, ON K2B 7M1<br>+5550123456<br>info@valeeight.com<br>www.valeeight.com</div>
    </header>
    <div class="letterhead__body">
      <p>Dear Client,</p>
      <p>Thank you for choosing our firm. We are pleased to confirm the details of your annual review and the planning steps we discussed at our recent meeting.</p>
      <p>Please find enclosed a summary of your current position, along with our notes on filing dates and the documents we will need from you this quarter.</p>
      <p>Should you have any questions, our team is happy to help by phone or email at any time.</p>
      <p>Yours Sincerely,</p>
    </div>
    <div class="letterhead__credentials"></div>
  </article>
  <article class="sheet envelope-back dl dl--letter">
    <div class="flap"><div class="wordmark">VALE 8</div></div>
  </article>
</section>

<section class="section section--dl">
  <article class="sheet envelope-back dl dl--back">
    <div class="flap"><div class="wordmark">VALE 8</div></div>
  </article>
  <article class="sheet dl--front">
    <div class="wordmark">VALE 8</div>
    <div class="tagline">CPAs and Tax Advisors</div>
    <div class="address">14 Harbor Ridge Lane,<br>Lakeview, ON K2B 7M1</div>
  </article>
</section>

<section class="section section--large">
  <article class="sheet envelope-back catalog">
    <div class="flap"><div class="wordmark">VALE 8</div></div>
  </article>
  <article class="sheet catalog-front">
    <div class="wordmark">VALE 8</div>
    <div class="tagline">CPAs and Tax Advisors</div>
    <div class="address">14 Harbor Ridge Lane,<br>Lakeview, ON K2B 7M1</div>
  </article>
</section>

</body>
</html>
```